web page look and feel - B2B enterprise application

We have an enterprise application with 10 to 15 core pages and several supporting pages or popups. To start, we want the graphical design of the Users, Roles and Data Source pages and their supporting popups, wizards, etc. to be made beautiful. That is around 10 pages in total. There is a fair amount of redundancy among the pages. I have attached 5 screenshots. We very much want the pages to project a premium feel. That is absolutely essential. The color scheme is blue and sometimes yellow (only if it makes the page look better) plus black, gray and white. If the design of these screens goes well, we would expand the project to continue with other pages. The core of what we are looking for is graphic in nature but we are open to workflow suggestions if you have them. The Roles screen needs some improvements to the layout. I am looking for everything that includes icons, fonts, spacing, etc. I assume getting to the final design will take some back and forth with multiple revisions.

Target Market(s)

Large Enterprises

Number of Pages Required

5+ page

Requirements
Must have
• Premium feel

```html
<!DOCTYPE html>
<html lang="en">
<head>
<meta charset="utf-8">
<title>Users – Norvale Data</title>
<link href="https://fonts.googleapis.com/css2?family=Roboto:wght@300;400;500&display=swap" rel="stylesheet">
<style>
:root{
  --header-dark:#141414;
  --header-mid:#2a2a2a;
  --sidebar:#2a4ea6;
  --sidebar-active:#1e2d5e;
  --sidebar-line:#3d60b6;
  --sidebar-muted:#8ea4d8;
  --navy:#1e3479;
  --yellow:#f7b91c;
  --content-bg:#e3e3e3;
  --row-alt:#f1f1f1;
  --row-line:#c9c9c9;
  --text:#2b2b2b;
  --muted:#6a6a6a;
  --white:#ffffff;
  --footer:#f6f6f6;
  --icon-blue:#5676c2;
}
*{box-sizing:border-box;margin:0;padding:0}
html,body{width:1200px;height:776px;overflow:hidden}
body{font-family:"Roboto",sans-serif;color:var(--text);background:var(--content-bg);position:relative}
.abs{position:absolute}
.topbar{left:0;top:0;width:1200px;height:91px;background:linear-gradient(180deg,var(--header-mid),var(--header-dark))}
.brand{left:46px;top:28px;display:flex;align-items:center;gap:10px;color:var(--white);font-size:23px;font-weight:500}
.brand-dot{width:14px;height:14px;border-radius:50%;background:var(--yellow)}
.hamburger{left:268px;top:29px}
.tool{top:33px}
.tool-sep{top:33px;width:1px;height:21px;background:#555}
.avatar{left:1032px;top:24px;width:37px;height:37px;border-radius:50%;background:linear-gradient(135deg,#8c8275,#3b3a38);border:2px solid #666}
.user-name{left:1075px;top:35px;color:var(--white);font-size:13.5px;display:flex;align-items:center;gap:6px}
.sidebar{left:0;top:91px;width:235px;height:626px;background:var(--sidebar)}
.nav-item{position:absolute;left:0;width:235px;color:var(--white);font-size:12.5px;font-weight:500;display:flex;align-items:center;gap:11px;padding-left:30px;border-bottom:1px solid var(--sidebar-line);white-space:nowrap}
.nav-item.active{background:var(--sidebar-active);border:none}
.nav-sub{position:absolute;left:57px;font-size:12px;color:var(--sidebar-muted);letter-spacing:.2px}
.pagehead{left:235px;top:91px;width:965px;height:65px;background:var(--white)}
.page-title{left:271px;top:117px;font-size:19px;font-weight:500;color:var(--text)}
.btn-add{left:364px;top:110px;width:81px;height:30px;border:2px solid var(--navy);border-radius:16px;color:var(--navy);font-size:15px;font-weight:500;display:flex;align-items:center;justify-content:center}
.search{left:874px;top:104px;width:277px;height:31px;border:1px solid #bdbdbd;border-radius:16px;display:flex;align-items:center;gap:8px;padding-left:13px;font-size:11.5px;color:#9a9a9a}
.adv-search{left:1060px;top:138px;font-size:11.5px;color:var(--muted)}
.btn-edit{left:1097px;top:164px;width:54px;height:22px;border-radius:11px;background:var(--yellow);font-size:12px;color:var(--text);display:flex;align-items:center;justify-content:center}
.card{left:275px;top:190px;width:886px;height:452px;background:var(--white);box-shadow:0 1px 3px rgba(0,0,0,.2)}
.thead{left:275px;top:190px;width:886px;height:27px;background:var(--yellow)}
.thead .first{position:absolute;left:0;top:0;width:133px;height:27px;background:var(--header-dark)}
.th{position:absolute;top:197px;font-size:12px;display:flex;align-items:center;gap:4px}
.selected{left:275px;top:217px;width:886px;height:29px;background:#1a1a1a;color:var(--white);font-size:12px}
.selected span{position:absolute;top:9px}
.detail{left:285px;top:246px;width:865px;height:152px;border:1px solid var(--row-line);border-top:none}
.drow{position:absolute;left:0;width:863px;height:29px;font-size:12px;border-bottom:1px solid var(--row-line)}
.drow.alt{background:var(--row-alt)}
.drow span{position:absolute;top:8px}
.perm{display:flex;align-items:center;gap:4px}
.urow{position:absolute;left:285px;width:865px;height:29px;font-size:12px;border:1px solid var(--row-line);border-top:none;background:var(--row-alt)}
.urow.light{background:var(--white)}
.urow span{position:absolute;top:8px}
.urow i{position:absolute;top:0;width:1px;height:28px;background:var(--row-line)}
.actions{position:absolute;right:8px;top:5px;display:flex;gap:4px}
.pager{left:285px;top:540px;width:865px;height:38px;border:1px solid var(--row-line);border-top:none}
.pill{position:absolute;top:9px;height:22px;border:1.5px solid var(--navy);border-radius:11px;font-size:11px;color:var(--navy);display:flex;align-items:center;justify-content:center;gap:4px}
.page-current{position:absolute;left:362px;top:9px;width:24px;height:24px;border-radius:50%;background:var(--navy);color:var(--white);font-size:11px;display:flex;align-items:center;justify-content:center}
.footer{left:0;top:717px;width:1200px;height:59px;background:var(--footer);display:flex;align-items:center;justify-content:center;font-size:12.5px;color:#777;font-weight:300}
</style>
</head>
<body>
<header class="abs topbar"></header>
<div class="abs brand"><span class="brand-dot"></span>Norvale Data</div>
<svg class="abs hamburger" width="26" height="20" viewBox="0 0 26 20"><g fill="#fff"><rect width="26" height="3.5" rx="1"/><rect y="8" width="26" height="3.5" rx="1"/><rect y="16" width="26" height="3.5" rx="1"/></g></svg>

<svg class="abs tool" style="left:796px" width="20" height="20" viewBox="0 0 20 20"><path d="M3 17 L14 6" stroke="#bbb" stroke-width="3" stroke-linecap="round"/><path d="M15 1v4M13 3h4M18 7v3M16.5 8.5h3" stroke="#bbb" stroke-width="1.3"/></svg>
<div class="abs tool-sep" style="left:832px"></div>
<svg class="abs tool" style="left:851px" width="20" height="20" viewBox="0 0 20 20"><circle cx="10" cy="10" r="6.5" fill="none" stroke="#bbb" stroke-width="4" stroke-dasharray="3 2.1"/><circle cx="10" cy="10" r="5" fill="#bbb"/><circle cx="10" cy="10" r="2.2" fill="#222"/></svg>
<div class="abs tool-sep" style="left:892px"></div>
<svg class="abs tool" style="left:913px" width="20" height="20" viewBox="0 0 20 20"><circle cx="10" cy="10" r="9.5" fill="#bbb"/><path d="M7.2 7.5a2.8 2.8 0 1 1 3.8 2.6c-.8.4-1 .8-1 1.7" stroke="#222" stroke-width="2" fill="none"/><circle cx="10" cy="15" r="1.2" fill="#222"/></svg>
<div class="abs tool-sep" style="left:954px"></div>
<svg class="abs tool" style="left:972px" width="23" height="20" viewBox="0 0 23 20"><path d="M1.5 16a10 10 0 0 1 20 0z" fill="#bbb"/><circle cx="6" cy="11" r="1.4" fill="#222"/><circle cx="8.5" cy="7" r="1.4" fill="#222"/><circle cx="14.5" cy="7" r="1.4" fill="#222"/><circle cx="17" cy="11" r="1.4" fill="#222"/><path d="M11.5 15l3-6" stroke="#222" stroke-width="2"/></svg>
<div class="abs tool-sep" style="left:1013px"></div>
<div class="abs avatar" role="img" aria-label="User profile photo"></div>
<div class="abs user-name">ORIN HALVIK <svg width="12" height="8" viewBox="0 0 12 8"><path d="M1 1l5 5 5-5" stroke="#fff" stroke-width="2" fill="none"/></svg></div>

<nav class="abs sidebar">
  <div class="nav-item active" style="top:0;height:48px">
    <svg width="16" height="16" viewBox="0 0 16 16" fill="none" stroke="#fff" stroke-width="1.4"><circle cx="8" cy="5" r="3.5"/><path d="M1.5 15c0-3.5 3-5.5 6.5-5.5s6.5 2 6.5 5.5z"/></svg>USERS</div>
  <div class="nav-sub" style="top:55px">ROLES</div>
  <div class="nav-sub" style="top:78px">NOTIFICATION GROUPS</div>
  <div class="abs" style="left:0;top:103px;width:235px;height:1px;background:var(--sidebar-line)"></div>
  <div class="nav-item" style="top:104px;height:44px;align-items:flex-start;padding-top:12px;border:none">
    <svg width="17" height="16" viewBox="0 0 17 16" fill="#cfd9f1"><rect x="6" y="0" width="5" height="4"/><rect x="0" y="11" width="5" height="5"/><rect x="6" y="11" width="5" height="5"/><rect x="12" y="11" width="5" height="5"/><path d="M8.5 4v7M2.5 11V7.5h12V11" stroke="#cfd9f1" stroke-width="1.3" fill="none"/></svg>DATA SOURCES</div>
  <div class="nav-sub" style="top:136px;color:#6f8bcd">DATA OBJECT RELATIONSHIP</div>
  <div class="abs" style="left:0;top:157px;width:235px;height:1px;background:var(--sidebar-line)"></div>
  <div class="nav-item" style="top:158px;height:35px">
    <svg width="16" height="17" viewBox="0 0 16 17" fill="#cfd9f1"><ellipse cx="8" cy="3" rx="8" ry="3"/><path d="M0 5.5c0 1.7 3.6 3 8 3s8-1.3 8-3v3c0 1.7-3.6 3-8 3s-8-1.3-8-3zM0 11c0 1.7 3.6 3 8 3s8-1.3 8-3v3c0 1.7-3.6 3-8 3s-8-1.3-8-3z"/></svg>DATA SETS</div>
  <div class="nav-item" style="top:193px;height:42px">
    <svg width="17" height="16" viewBox="0 0 17 16" fill="none" stroke="#cfd9f1" stroke-width="1.3"><rect x="2" y="1" width="13" height="14"/><path d="M5 5h7M5 8h7M5 11h5M0 1h2"/></svg>RULE SETS</div>
  <div class="nav-item" style="top:235px;height:38px">
    <svg width="16" height="16" viewBox="0 0 16 16" fill="none" stroke="#cfd9f1" stroke-width="1.3"><rect x="1" y="2.5" width="14" height="12.5"/><path d="M4 0v4M12 0v4M1 6h14"/><path d="M4 9h1M7.5 9h1M11 9h1M4 12h1M7.5 12h1M11 12h1" stroke-width="1.6"/></svg>SCHEDULES</div>
  <div class="nav-item" style="top:273px;height:42px">
    <svg width="18" height="14" viewBox="0 0 18 14" fill="none" stroke="#cfd9f1" stroke-width="1.5"><path d="M1 4h15M12 1l4 3-4 3M17 10H2M6 7l-4 3 4 3"/></svg>METADATA IMPORT / EXPORT</div>
</nav>

<div class="abs pagehead"></div>
<h1 class="abs page-title">USERS</h1>
<div class="abs btn-add">ADD</div>
<div class="abs search"><svg width="14" height="14" viewBox="0 0 14 14" fill="none" stroke="#8a8a8a" stroke-width="1.8"><circle cx="6" cy="6" r="4.6"/><path d="M9.5 9.5L13 13"/></svg>Search here</div>
<div class="abs adv-search">Advanced Search</div>
<div class="abs btn-edit">Edit</div>

<section class="abs card"></section>
<div class="abs thead"><div class="first"></div></div>
<div class="th" style="left:308px;color:#fff">First Name <svg width="10" height="7" viewBox="0 0 10 7"><path d="M1 1l4 4 4-4" stroke="#fff" stroke-width="1.8" fill="none"/></svg></div>
<div class="th" style="left:439px">Last Name <svg width="10" height="7" viewBox="0 0 10 7"><path d="M1 1l4 4 4-4" stroke="#222" stroke-width="1.8" fill="none"/></svg></div>
<div class="th" style="left:576px">Username <svg width="10" height="7" viewBox="0 0 10 7"><path d="M1 1l4 4 4-4" stroke="#222" stroke-width="1.8" fill="none"/></svg></div>
<div class="th" style="left:725px">Email address <svg width="10" height="7" viewBox="0 0 10 7"><path d="M1 1l4 4 4-4" stroke="#222" stroke-width="1.8" fill="none"/></svg></div>
<div class="th" style="left:920px">Status <svg width="10" height="7" viewBox="0 0 10 7"><path d="M1 1l4 4 4-4" stroke="#222" stroke-width="1.8" fill="none"/></svg></div>

<div class="abs selected">
  <svg style="position:absolute;left:11px;top:11px" width="10" height="7" viewBox="0 0 10 7"><path d="M1 1l4 4 4-4" stroke="#fff" stroke-width="1.6" fill="none"/></svg>
  <span style="left:34px">Tim</span><span style="left:165px">Tim</span><span style="left:302px">tim.timtim</span><span style="left:450px">tim@corvia.example</span><span style="left:648px">Active</span>
  <svg style="position:absolute;left:799px;top:4px" width="70" height="21" viewBox="0 0 70 21" fill="none" stroke="#fff" stroke-width="1.3"><circle cx="10.5" cy="10.5" r="9.5"/><path d="M7 14l1-3 5-5 2 2-5 5zM6.5 6.5h4"/><circle cx="33" cy="10.5" r="9.5"/><rect x="28.5" y="8" width="6" height="7"/><path d="M31 8V6h6v7h-2.5"/><circle cx="55.5" cy="10.5" r="9.5"/><path d="M51.5 7.5h8M53 7.5l.6 8h3.8l.6-8M54 6h3M54.8 9.5v4.5M56.2 9.5v4.5"/></svg>
</div>

<div class="abs detail">
  <div class="drow" style="top:0"><span style="left:23px;top:12px">Object</span><span style="left:365px;top:9px">Permissions</span></div>
  <div class="drow alt" style="top:30px"><span style="left:23px">System Settings</span><span class="perm" style="left:363px;top:6px">
    <svg width="15" height="15" viewBox="0 0 15 15" fill="none" stroke="#2a4ea6" stroke-width="1.4"><circle cx="7.5" cy="7.5" r="6.5"/><path d="M4.5 7.8l2.2 2.2 4-4.3"/></svg>Read&nbsp;&nbsp;<svg width="15" height="15" viewBox="0 0 15 15" fill="none" stroke="#2a4ea6" stroke-width="1.4"><circle cx="7.5" cy="7.5" r="6.5"/><path d="M4.5 7.8l2.2 2.2 4-4.3"/></svg>Write</span></div>
  <div class="drow" style="top:59px"><span style="left:23px">Users</span><span class="perm" style="left:363px;top:6px">
    <svg width="15" height="15" viewBox="0 0 15 15" fill="none" stroke="#2a4ea6" stroke-width="1.4"><circle cx="7.5" cy="7.5" r="6.5"/><path d="M4.5 7.8l2.2 2.2 4-4.3"/></svg>Read&nbsp;&nbsp;<svg width="15" height="15" viewBox="0 0 15 15" fill="none" stroke="#2a4ea6" stroke-width="1.4"><circle cx="7.5" cy="7.5" r="6.5"/><path d="M4.5 7.8l2.2 2.2 4-4.3"/></svg>Write</span></div>
  <div class="drow alt" style="top:88px"><span style="left:23px">Data Source</span><span style="left:365px;top:6px">Role</span></div>
  <div class="drow" style="top:117px;height:34px;border:none"><span style="left:23px;top:10px">All Data Sources</span><span style="left:365px;top:7px">System Administrator</span></div>
</div>

<div class="urow" style="top:398px;border-top:1px solid var(--row-line)"><span style="left:24px">Test</span><i style="left:108px"></i><span style="left:157px">User</span><i style="left:251px"></i><span style="left:303px">test.User</span><i style="left:401px"></i><span style="left:440px">testuser999@mailbox.example</span><i style="left:615px"></i><span style="left:644px">Active</span>
  <svg class="actions" width="66" height="19" viewBox="0 0 66 19" fill="none" stroke="#5676c2" stroke-width="1.1"><circle cx="9.5" cy="9.5" r="8.8"/><path d="M6.5 12.8l.9-2.7 4.4-4.4 1.8 1.8-4.4 4.4zM6 6h3.5"/><circle cx="32.5" cy="9.5" r="8.8"/><rect x="28.5" y="7.5" width="5.4" height="6.3"/><path d="M30.7 7.5V5.7h5.4v6.3h-2.2"/><circle cx="55.5" cy="9.5" r="8.8"/><path d="M51.8 6.8h7.4M53.2 6.8l.6 7.2h3.4l.6-7.2M54 5.4h3M54.7 8.6v4M56.3 8.6v4"/></svg></div>
<div class="urow light" style="top:427px"><span style="left:24px">Test</span><i style="left:108px"></i><span style="left:157px">Test</span><i style="left:251px"></i><span style="left:303px">test.Test</span><i style="left:401px"></i><span style="left:440px">test@test.example</span><i style="left:615px"></i><span style="left:644px">Active</span>
  <svg class="actions" width="66" height="19" viewBox="0 0 66 19" fill="none" stroke="#5676c2" stroke-width="1.1"><circle cx="9.5" cy="9.5" r="8.8"/><path d="M6.5 12.8l.9-2.7 4.4-4.4 1.8 1.8-4.4 4.4zM6 6h3.5"/><circle cx="32.5" cy="9.5" r="8.8"/><rect x="28.5" y="7.5" width="5.4" height="6.3"/><path d="M30.7 7.5V5.7h5.4v6.3h-2.2"/><circle cx="55.5" cy="9.5" r="8.8"/><path d="M51.8 6.8h7.4M53.2 6.8l.6 7.2h3.4l.6-7.2M54 5.4h3M54.7 8.6v4M56.3 8.6v4"/></svg></div>
<div class="urow" style="top:456px"><span style="left:24px">Sam</span><i style="left:108px"></i><span style="left:157px">Carver</span><i style="left:251px"></i><span style="left:303px">sam.Carver</span><i style="left:401px"></i><span style="left:440px">sam@norvale.example</span><i style="left:615px"></i><span style="left:644px">Active</span>
  <svg class="actions" width="66" height="19" viewBox="0 0 66 19" fill="none" stroke="#5676c2" stroke-width="1.1"><circle cx="9.5" cy="9.5" r="8.8"/><path d="M6.5 12.8l.9-2.7 4.4-4.4 1.8 1.8-4.4 4.4zM6 6h3.5"/><circle cx="32.5" cy="9.5" r="8.8"/><rect x="28.5" y="7.5" width="5.4" height="6.3"/><path d="M30.7 7.5V5.7h5.4v6.3h-2.2"/><circle cx="55.5" cy="9.5" r="8.8"/><path d="M51.8 6.8h7.4M53.2 6.8l.6 7.2h3.4l.6-7.2M54 5.4h3M54.7 8.6v4M56.3 8.6v4"/></svg></div>
<div class="urow light" style="top:485px"><span style="left:24px">Orin</span><i style="left:108px"></i><span style="left:157px">Halvik</span><i style="left:251px"></i><span style="left:303px">orhal.test</span><i style="left:401px"></i><span style="left:440px">tom@ridgeway.example</span><i style="left:615px"></i><span style="left:644px">Active</span>
  <svg class="actions" width="66" height="19" viewBox="0 0 66 19" fill="none" stroke="#5676c2" stroke-width="1.1"><circle cx="9.5" cy="9.5" r="8.8"/><path d="M6.5 12.8l.9-2.7 4.4-4.4 1.8 1.8-4.4 4.4zM6 6h3.5"/><circle cx="32.5" cy="9.5" r="8.8"/><rect x="28.5" y="7.5" width="5.4" height="6.3"/><path d="M30.7 7.5V5.7h5.4v6.3h-2.2"/><circle cx="55.5" cy="9.5" r="8.8"/><path d="M51.8 6.8h7.4M53.2 6.8l.6 7.2h3.4l.6-7.2M54 5.4h3M54.7 8.6v4M56.3 8.6v4"/></svg></div>
<div class="urow" style="top:514px"><span style="left:24px">Beck</span><i style="left:108px"></i><span style="left:157px">Thorne</span><i style="left:251px"></i><span style="left:303px">beck.Thorne</span><i style="left:401px"></i><span style="left:440px">biff@mailbox.example</span><i style="left:615px"></i><span style="left:644px">Active</span>
  <svg class="actions" width="66" height="19" viewBox="0 0 66 19" fill="none" stroke="#5676c2" stroke-width="1.1"><circle cx="9.5" cy="9.5" r="8.8"/><path d="M6.5 12.8l.9-2.7 4.4-4.4 1.8 1.8-4.4 4.4zM6 6h3.5"/><circle cx="32.5" cy="9.5" r="8.8"/><rect x="28.5" y="7.5" width="5.4" height="6.3"/><path d="M30.7 7.5V5.7h5.4v6.3h-2.2"/><circle cx="55.5" cy="9.5" r="8.8"/><path d="M51.8 6.8h7.4M53.2 6.8l.6 7.2h3.4l.6-7.2M54 5.4h3M54.7 8.6v4M56.3 8.6v4"/></svg></div>

<div class="abs pager">
  <div class="pill" style="left:306px;width:51px">PREV</div>
  <div class="page-current">01</div>
  <div class="pill" style="left:391px;width:50px">NEXT</div>
  <div class="pill" style="left:452px;width:51px;color:#333">20 <svg width="9" height="6" viewBox="0 0 9 6"><path d="M1 1l3.5 3.5L8 1" stroke="#333" stroke-width="1.2" fill="none"/></svg></div>
</div>

<footer class="abs footer">© 2018 Company Name&nbsp;&nbsp;All right reserved</footer>
</body>
</html>
```